English and Spanish Language School Needs a Business Card

Need a business card design a startup company called Maribel Language School. The company will offer English and Spanish conversational level courses designed to make the learner feel comfortable with grammar and vocabulary. We would like to see a logo with some colour that should communicate learning, growth.

Target Market(s)

Consumers and businesses

Industry/Entity Type

Education

Contact Information for Business Card

TBD

Font styles to use
Serif

Requirements
Must have
• Include the following
• Logo
• Name
• Title
• Cellphone Number
• Office Phone number
• Email address
• Office Address

```html
<!DOCTYPE html>
<html lang="en">
<head>
<meta charset="UTF-8">
<title>Maribel Language School – Business Card</title>
<link href="https://fonts.googleapis.com/css2?family=Tinos:wght@400;700&display=swap" rel="stylesheet">
<style>
  :root {
    --canvas-bg: #e9e6e1;
    --card-white: #f7f7f5;
    --brand-red: #d3232f;
    --brand-red-deep: #b81d28;
    --brand-teal: #16b8c2;
    --text-light: #ffffff;
    --shadow: rgba(0, 0, 0, 0.18);
  }
  * { margin: 0; padding: 0; box-sizing: border-box; }
  html, body {
    width: 1200px;
    height: 780px;
    overflow: hidden;
    background: var(--canvas-bg);
    font-family: "Tinos", "Times New Roman", serif;
  }
  .canvas {
    position: relative;
    width: 1200px;
    height: 780px;
  }
  .card {
    position: absolute;
    width: 520px;
    height: 298px;
    border-radius: 16px;
    overflow: hidden;
    box-shadow: 0 10px 26px var(--shadow);
  }
  /* Front */
  .card-front {
    left: 50px;
    top: 241px;
    background: var(--card-white);
  }
  .front-brand {
    position: absolute;
    left: 0; top: 0;
    width: 100%;
    height: 130px;
    display: flex;
    align-items: center;
    padding-left: 48px;
    gap: 14px;
  }
  .brand-dot {
    width: 18px;
    height: 18px;
    border-radius: 50%;
    background: var(--brand-red);
    flex: none;
  }
  .brand-name {
    color: var(--brand-red);
    font-weight: 700;
    line-height: 1;
  }
  .brand-name .brand-main {
    display: block;
    font-size: 54px;
    letter-spacing: -0.5px;
  }
  .brand-name .brand-sub {
    display: block;
    font-size: 21px;
    margin-top: 4px;
    letter-spacing: 0.3px;
  }
  .front-band {
    position: absolute;
    left: 0; top: 130px;
    width: 100%;
    height: 30px;
    background: var(--brand-teal);
    color: var(--text-light);
    display: flex;
    align-items: center;
    padding-left: 48px;
    font-size: 16px;
  }
  .person-name { letter-spacing: 0.6px; }
  .divider {
    display: inline-block;
    width: 1px;
    height: 16px;
    background: var(--text-light);
    margin: 0 8px;
  }
  .person-title { font-size: 14px; }
  .front-contact {
    position: absolute;
    left: 0; top: 160px;
    width: 100%;
    height: 138px;
    background: linear-gradient(135deg, var(--brand-red) 0%, var(--brand-red-deep) 100%);
    color: var(--text-light);
    padding: 22px 0 0 110px;
    font-size: 15px;
    line-height: 24px;
  }
  .contact-label { font-weight: 700; }
  /* Back */
  .card-back {
    left: 630px;
    top: 241px;
    background: radial-gradient(circle at 40% 35%, var(--brand-red) 0%, var(--brand-red-deep) 100%);
    display: flex;
    align-items: center;
    justify-content: center;
  }
  .card-back .brand-name { color: var(--text-light); }
  .card-back .brand-main { font-size: 72px; }
  .card-back .brand-sub { font-size: 26px; margin-top: 6px; }
</style>
</head>
<body>
<main class="canvas">
  <section class="card card-front" aria-label="Business card front">
    <div class="front-brand">
      <span class="brand-dot"></span>
      <h1 class="brand-name">
        <span class="brand-main">Maribel</span>
        <span class="brand-sub">Language School</span>
      </h1>
    </div>
    <div class="front-band">
      <span class="person-name">DANIEL REYES</span>
      <span class="divider"></span>
      <span class="person-title">Manager</span>
    </div>
    <div class="front-contact">
      <p><span class="contact-label">M:</span> 123 456 7890</p>
      <p><span class="contact-label">O:</span> 123 456 7890</p>
      <p>your@yourcompany.com</p>
      <p>Your Address,2nd Ste, Fairhaven, Texas 1234</p>
    </div>
  </section>

  <section class="card card-back" aria-label="Business card back">
    <h2 class="brand-name">
      <span class="brand-main">Maribel</span>
      <span class="brand-sub">Language School</span>
    </h2>
  </section>
</main>
</body>
</html>
```